Keystone Trench Co Business Card*

Looking for a professional, clean and crisp business card

I am in the underground utilities industry and am just looking for a really impressive business card. I would like our card to be white with our symbol crisp and clear with it protruding. I also have a business partner that will require his name and info on the card once the design is set. I would like to have our website info on the card which is;
http://keystonetrenchco.example/

Contact Information for Business Card

Website, contact name, number and email

```html
<!DOCTYPE html>
<html lang="en">
<head>
<meta charset="utf-8">
<title>Keystone Trench Co Business Card</title>
<link href="https://fonts.googleapis.com/css2?family=Saira+Condensed:wght@700&family=Montserrat:wght@400;500&display=swap" rel="stylesheet">
<style>
  :root {
    --stage: #1c1c1e;
    --card-dark: #0b0c0e;
    --card-dark-2: #1b1f26;
    --card-white: #ffffff;
    --ink: #2a3340;
    --blue: #3a5fa8;
    --band-dark: #2f3742;
    --text: #1e1e1e;
  }
  * { box-sizing: border-box; margin: 0; padding: 0; }
  html, body { width: 1200px; height: 900px; overflow: hidden; }
  body {
    background: var(--stage);
    font-family: "Montserrat", sans-serif;
    position: relative;
  }
  .card {
    position: absolute;
    left: 250px;
    width: 700px;
    height: 400px;
    overflow: hidden;
    box-shadow: 0 12px 30px rgba(0,0,0,.5);
  }
  .card--back { top: 30px; background: var(--card-dark); }
  .card--front { top: 470px; background: var(--card-white); }

  .back-pattern {
    position: absolute; inset: 0;
    background: linear-gradient(135deg, var(--card-dark) 0%, var(--card-dark-2) 50%, var(--card-dark) 100%);
  }
  .brand {
    position: absolute;
    display: flex; align-items: center; gap: 12px;
    font-family: "Saira Condensed", sans-serif;
    font-weight: 700;
    text-transform: uppercase;
    letter-spacing: 1px;
  }
  .brand__dot { width: 22px; height: 22px; border-radius: 50%; }
  .card--back .brand { right: 50px; top: 170px; color: #fff; font-size: 40px; }
  .card--back .brand__dot { background: var(--blue); }
  .card--front .brand { left: 60px; top: 80px; color: var(--ink); font-size: 40px; }
  .card--front .brand__dot { background: var(--blue); }

  .person {
    position: absolute; left: 360px; top: 215px;
  }
  .person__name {
    font-family: "Saira Condensed", sans-serif;
    font-weight: 700;
    font-size: 34px;
    letter-spacing: 1.5px;
    color: var(--ink);
    text-transform: uppercase;
  }
  .person__rule { width: 20px; height: 2px; background: var(--blue); margin: 8px 0 16px; }
  .contact { list-style: none; font-size: 17px; color: var(--text); }
  .contact li { display: flex; align-items: center; gap: 10px; margin-bottom: 6px; }
  .contact svg { width: 18px; height: 18px; flex: none; }
  .contact .accent { color: var(--blue); }

  .band { position: absolute; bottom: 0; }
  .band--blue { left: 0; width: 300px; height: 34px; background: var(--blue); }
  .band--dark { left: 300px; right: 0; height: 18px; background: var(--band-dark); }
</style>
</head>
<body>
  <section class="card card--back" aria-label="Card back">
    <div class="back-pattern" role="img" aria-label="Dark diagonal pattern of pipe sections"></div>
    <div class="brand"><span class="brand__dot"></span>Keystone Trench Co</div>
  </section>

  <section class="card card--front" aria-label="Card front">
    <div class="brand"><span class="brand__dot"></span>Keystone Trench Co</div>
    <div class="person">
      <h1 class="person__name">Dale Marrow</h1>
      <div class="person__rule"></div>
      <ul class="contact">
        <li>
          <svg viewBox="0 0 24 24" fill="none" stroke="#3a5fa8" stroke-width="2"><path d="M5 3h4l2 5-2.5 1.5a11 11 0 0 0 6 6L16 13l5 2v4a2 2 0 0 1-2 2A16 16 0 0 1 3 5a2 2 0 0 1 2-2z"/></svg>
          555-014-2387
        </li>
        <li>
          <svg viewBox="0 0 24 24" fill="none" stroke="#3a5fa8" stroke-width="2"><rect x="3" y="5" width="18" height="14"/><path d="M3 5l9 8 9-8"/></svg>
          dale@keystonetrenchco.example
        </li>
        <li>
          <svg viewBox="0 0 24 24" fill="none" stroke="#3a5fa8" stroke-width="2"><circle cx="12" cy="12" r="9"/><path d="M3 12h18M12 3a14 14 0 0 1 0 18M12 3a14 14 0 0 0 0 18"/></svg>
          <span>www.<span class="accent">keystonetrenchco</span>.example</span>
        </li>
      </ul>
    </div>
    <div class="band band--blue"></div>
    <div class="band band--dark"></div>
  </section>
</body>
</html>
```